MAPLE HOLLOW TOPICAL BOX W LABEL

This one will be a new design for me, so I may need to feel some things out.
My idea is to have some/ half iridescent, with white (top portion) and iridescent stamped logo
I googled my idea and found some pictures to help explain the style
Maybe an iridescent or white part may also be a palm tree ?
The name of the topical is
MAPLE HOLLOW
I'm not sure how to design the name on the front, but i dont expect it like the Jade Ember
The warnings and such are all the same from the other topicals. I will update the ingredients mostly and any other variable parts.

```html
<!DOCTYPE html>
<html lang="en">
<head>
<meta charset="utf-8">
<title>Orla's Maple Hollow – Jar Label</title>
<link href="https://fonts.googleapis.com/css2?family=Roboto+Condensed:wght@300;400&family=Jost:wght@400;500&family=DM+Serif+Display&family=EB+Garamond:wght@400&family=Arimo:wght@700&display=swap" rel="stylesheet">
<style>
  :root {
    --ink: #2a3585;
    --backdrop: #d4d4d4;
    --label: #ffffff;
    --brand-foil: #a9b6e0;
    --shimmer-a: #e9b7b0;
    --shimmer-b: #9fc9e3;
    --shimmer-c: #f2e49a;
    --shimmer-d: #9fd6c0;
    --caption: #111111;
  }
  * { box-sizing: border-box; margin: 0; padding: 0; }
  html, body { width: 1200px; height: 1081px; overflow: hidden; }
  body { background: var(--backdrop); position: relative; font-family: "Roboto Condensed", sans-serif; color: var(--ink); }

  .label {
    position: absolute; left: 68px; top: 148px; width: 1064px; height: 199px;
    background: var(--label); border-radius: 12px;
  }
  .badges { position: absolute; left: 0; top: 4px; width: 360px; height: 84px; }
  .blurb {
    position: absolute; left: 8px; top: 92px; width: 338px;
    font-weight: 300; font-size: 11.2px; line-height: 11.35px; text-align: justify;
    letter-spacing: -0.15px;
  }
  .blurb p + p { margin-top: 5px; }

  .front { position: absolute; left: 400px; top: 0; width: 264px; height: 199px; text-align: center; }
  .front > * { position: absolute; left: -20px; right: -20px; }
  .brand-name {
    top: 12px; font-family: "DM Serif Display", serif; font-size: 72px; line-height: 72px;
    color: var(--brand-foil); letter-spacing: 1px;
  }
  .product-name {
    top: 98px; font-family: "Jost", sans-serif; font-weight: 500; font-size: 24px; line-height: 26px;
    letter-spacing: 7px; margin-right: -7px; white-space: nowrap;
  }
  .shimmer-rule {
    top: 127px; left: 0; right: 0; height: 3px;
    background: linear-gradient(90deg, var(--shimmer-d), var(--shimmer-b), var(--shimmer-a), var(--shimmer-c), var(--shimmer-d));
  }
  .product-sub { top: 132px; font-family: "Jost", sans-serif; font-size: 21px; line-height: 24px; white-space: nowrap; }
  .net-weight { top: 171px; font-family: "EB Garamond", serif; font-size: 11.5px; line-height: 14px; }

  .details {
    position: absolute; left: 717px; top: 10px; width: 338px;
    font-weight: 300; font-size: 11.2px; line-height: 11.35px; text-align: justify;
    letter-spacing: -0.15px;
  }
  .details p + p { margin-top: 5px; }

  .size-caption {
    position: absolute; left: 0; top: 397px; width: 1200px; text-align: center;
    font-family: "Arimo", sans-serif; font-weight: 700; font-size: 27px; color: var(--caption);
  }
</style>
</head>
<body>
  <section class="label">
    <svg class="badges" viewBox="0 0 360 84" aria-label="Product claim badges">
      <defs>
        <path id="arc-top" d="M 9 42 A 32 32 0 0 1 73 42"/>
        <path id="arc-bottom" d="M 2 42 A 39 39 0 0 0 80 42"/>
      </defs>
      <g font-family="Jost, sans-serif" font-size="8.6" fill="var(--ink)" letter-spacing="1.6">
        <g transform="translate(0,0)">
          <circle cx="41" cy="42" r="32" fill="none" stroke="var(--ink)" stroke-width="1.3" stroke-dasharray="24 26" stroke-dashoffset="-12"/>
          <text><textPath href="#arc-top" startOffset="50%" text-anchor="middle">ORGANIC</textPath></text>
          <text><textPath href="#arc-bottom" startOffset="50%" text-anchor="middle">INGREDIENTS</textPath></text>
          <rect x="28" y="28" width="26" height="27" rx="13" fill="var(--shimmer-b)" role="img" aria-label="Leaf icon"/>
        </g>
        <g transform="translate(90,0)">
          <circle cx="41" cy="42" r="32" fill="none" stroke="var(--ink)" stroke-width="1.3" stroke-dasharray="24 26" stroke-dashoffset="-12"/>
          <text><textPath href="#arc-top" startOffset="50%" text-anchor="middle">HIGH</textPath></text>
          <text><textPath href="#arc-bottom" startOffset="50%" text-anchor="middle">POTENCY</textPath></text>
          <path d="M 44 29 L 35 44 L 41 44 L 38 55 L 48 40 L 42 40 Z" fill="var(--shimmer-c)" stroke="var(--ink)" stroke-width="1"/>
        </g>
        <g transform="translate(181,0)">
          <circle cx="41" cy="42" r="32" fill="none" stroke="var(--ink)" stroke-width="1.3" stroke-dasharray="24 26" stroke-dashoffset="-12"/>
          <text><textPath href="#arc-top" startOffset="50%" text-anchor="middle">AWARD</textPath></text>
          <text><textPath href="#arc-bottom" startOffset="50%" text-anchor="middle">WINNING</textPath></text>
          <rect x="28" y="27" width="26" height="28" rx="13" fill="var(--shimmer-a)" role="img" aria-label="Medal icon"/>
        </g>
        <g transform="translate(271,0)">
          <circle cx="41" cy="42" r="32" fill="none" stroke="var(--ink)" stroke-width="1.3" stroke-dasharray="24 26" stroke-dashoffset="-12"/>
          <text><textPath href="#arc-top" startOffset="50%" text-anchor="middle">NATURAL</textPath></text>
          <text><textPath href="#arc-bottom" startOffset="50%" text-anchor="middle">HEALING</textPath></text>
          <rect x="26" y="27" width="30" height="28" rx="13" fill="var(--shimmer-d)" role="img" aria-label="Hand holding flower icon"/>
        </g>
      </g>
    </svg>

    <div class="blurb">
      <p>ORLA'S MAPLE HOLLOW is a harmonious synergy of botanial-rich actives embraced with natural and organic therapeutic oils overflowing with a high-content anti-inflammatory infusion and supercharged with THC. The intrinsic nature of this balm brings forth soothing relief and healing to the areas where you need it the most. The intelligence of this alchemized blend is characterized by its powerful relief and deeply calming comforts.</p>
      <p>Apply this deeply nourishing balm to anywhere on the body as a natural remedy to help calm, soothe and relieve troubled or painful areas. Best used within 6 months.</p>
    </div>

    <div class="front">
      <div class="brand-name">ORLA'S</div>
      <div class="product-name">MAPLE HOLLOW</div>
      <div class="shimmer-rule"></div>
      <div class="product-sub">with Argan, Coconut &amp; Aloe</div>
      <div class="net-weight">Net Weight 2oz (56g)</div>
    </div>

    <div class="details">
      <p>ORGANIC INGREDIENTS : Butyrospermum Parkii Butter (Shea Butter), Aloe Barbadensis (Aloe Vera) Leaf Extract, Coco Nucifera (Coconut) Oil, THC CANNABIS EXTRACT, Cannabis Sativa Seed Oil, Pure Cannabidol (Hemp Extract), Prunes Armeniaca (Apricot) Kernal Oil, Hydrogenated Vegetable (Soybean) Oil, Prunus Amygdalus Dulcis (Sweet Almond Oil), Vitus Vinifera (Grape) Seed Oil, Macadamia Ternifolia Seed Oil, Daucus Carota (Carrot) Seed Oil, Proprietary Blend of Therapeutic Essential Oils (including but not limited to : Lavender, Chamomile), Tocopherol (Vitamin E, antioxidant)</p>
      <p>Color is a Natural result of the Phytonutrients within the Formula and May Vary in Intensity. Consistency may also Vary. For Optimal Preservation, Keep in a Cool, Dark Place. Fatty Acids may Naturally Aggregate when Exposed to Temperature Extremes Forming Beads. To Fix This, Use a Hair Dryer to Melt them Back to a Smooth Consistency. For Best Results, Apply to Skin after a warm wash. Botanical oils and Healing compounds are better able to lock into the dermis when the pores are clean, warm and open.</p>
    </div>
  </section>

  <div class="size-caption">6 Inch x 1.125 Inch</div>
</body>
</html>
```